Modern Business Card for Larkwell 2018

Our company assumes the best about people. We are creating an online community of entrepreneurs and business leaders who struggle with marketing their business online.

This business card should POP! We recently got a new logo and are launching a new website next month, so our business cards should make a statement that feels:
-Fresh
-Smart
-Trustworthy
-Fun

Target Market(s)

small business owners, entrepreneurs

Industry/Entity Type

Digital Marketing

Contact Information for Business Card

Dimensions: 3.5" x 2"

Font styles to use
Sans Serif

Colors
f37122
ffffff

Requirements
Must have
• We need a business card with a modern, bold design. We will use one side of the card as a lead-generation offer, so text on one side will need to fit up to 140 characters. The business card should stick to our core colors (orange, black, and white).
Nice to have
• We think a vertical "portrait" design could be interesting.
Should not have
• Should not look like a traditional business card. The round icon should stand out from a distance.

```html
<!DOCTYPE html>
<html lang="en">
<head>
<meta charset="utf-8">
<title>Larkwell Business Card</title>
<link href="https://fonts.googleapis.com/css2?family=Roboto:wght@400;500;700;900&family=Kaushan+Script&display=swap" rel="stylesheet">
<style>
  :root {
    --orange: #f37122;
    --white: #ffffff;
    --card-white: #f4f4f3;
    --ink: #111111;
    --backdrop: #e8e5e1;
    --rule: #2a2a2a;
  }
  * { margin: 0; padding: 0; box-sizing: border-box; }
  html, body {
    width: 1200px; height: 960px; overflow: hidden;
    background: var(--backdrop);
    font-family: "Roboto", Arial, sans-serif;
  }
  .card {
    position: absolute;
    width: 598px; height: 342px;
    border-radius: 22px;
    overflow: hidden;
    background: var(--card-white);
    box-shadow: 0 3px 8px rgba(0,0,0,0.25);
  }
  .card-front { left: 315px; top: 113px; }
  .card-back { left: 312px; top: 473px; }

  .front-art { position: absolute; inset: 0; }
  .brand-mark {
    position: absolute; left: 63px; top: 30px;
    display: flex; flex-direction: column; align-items: center; gap: 10px;
  }
  .brand-dot {
    width: 124px; height: 124px; border-radius: 50%;
    background: var(--orange);
  }
  .brand-name-front {
    font-weight: 900; font-size: 22px; letter-spacing: 2px;
    color: var(--orange);
  }
  .identity {
    position: absolute; right: 45px; top: 218px;
    text-align: right; color: var(--ink);
  }
  .person-name {
    font-family: "Kaushan Script", cursive;
    font-size: 30px; line-height: 1; letter-spacing: 0;
    white-space: nowrap;
  }
  .person-role {
    margin-top: 13px; font-size: 16px; font-weight: 500; letter-spacing: 0.3px;
  }
  .person-email { margin-top: 5px; font-size: 14px; }

  .offer-band {
    position: absolute; left: 0; top: 0; width: 100%; height: 217px;
    background: var(--orange); color: var(--white);
  }
  .lockup {
    position: absolute; left: 40px; top: 55px; width: 240px;
    display: flex; flex-direction: column; align-items: center;
  }
  .lockup-dot {
    width: 36px; height: 36px; border-radius: 50%; background: var(--white);
  }
  .lockup-name {
    margin-top: 12px; font-size: 37px; font-weight: 900; letter-spacing: 1.5px; line-height: 1;
  }
  .lockup-tagline {
    margin-top: 7px; font-size: 11px; font-weight: 500; letter-spacing: 1.3px;
  }
  .divider {
    position: absolute; left: 297px; top: 27px; width: 1px; height: 165px;
    background: rgba(255,255,255,0.75);
  }
  .offer {
    position: absolute; left: 322px; top: 30px; width: 260px;
  }
  .offer-headline {
    font-size: 18.5px; font-weight: 700; line-height: 21px; letter-spacing: 0.2px;
  }
  .offer-copy { margin-top: 7px; font-size: 14.5px; line-height: 20px; }
  .offer-link { margin-top: 8px; font-size: 19px; font-weight: 700; }
  .note-lines { position: absolute; left: 35px; right: 44px; top: 259px; }
  .note-line { height: 1px; background: var(--rule); margin-bottom: 39px; }
</style>
</head>
<body>
  <section class="card card-front">
    <svg class="front-art" viewBox="0 0 598 342" width="598" height="342">
      <path d="M268,0 C320,40 330,110 282,182 C244,240 222,300 262,342 L275,342 C236,300 258,240 296,182 C344,110 334,40 282,0 Z" fill="var(--ink)"/>
      <path d="M278,0 C330,40 340,110 292,182 C254,240 234,300 276,342 L598,342 L598,0 Z" fill="var(--orange)"/>
    </svg>
    <div class="brand-mark">
      <div class="brand-dot"></div>
      <div class="brand-name-front">LARKWELL</div>
    </div>
    <div class="identity">
      <div class="person-name">DANA WHITFIELD</div>
      <div class="person-role">STORY MARKETING COACH</div>
      <div class="person-email">dana@larkwellnow.com</div>
    </div>
  </section>

  <section class="card card-back">
    <div class="offer-band">
      <div class="lockup">
        <div class="lockup-dot"></div>
        <div class="lockup-name">LARKWELL</div>
        <div class="lockup-tagline">TELL STORIES THAT INSPIRE ACTION</div>
      </div>
      <div class="divider"></div>
      <div class="offer">
        <div class="offer-headline">REACH MORE PEOPLE.<br>MAKE MORE MONEY.<br>CREATE MORE IMPACT.</div>
        <div class="offer-copy">Get your free Larkwell<br>Starter Package and our<br>marketing guide today at</div>
        <div class="offer-link">Larkwellnow.com/start</div>
      </div>
    </div>
    <div class="note-lines">
      <div class="note-line"></div>
      <div class="note-line"></div>
    </div>
  </section>
</body>
</html>
```